Business Card Re-Design/Update

We'd like to update out business cards. I've included our current "Style guide" which has the colour scheme of the organisation in it. I've also included the branding files with logos etc in them.

I've also included a copy of one of our existing cards so that you can see how ugly/dated they look. I'd like a fresh modern corporate look.

Target Market(s)

These are for our clients, potential clients, industry contacts - like all business cards

Contact Information for Business Card

Name
Position
Company Address - Level 1, 47 Fernby Street, Carlow Qld 4072
Direct Phone
mobile
Email
Website -www.korvalit.com.au
Logo

Colors

Designer to choose colors to be used in the design.

Requirements
Must have
• Main Logo
• Cards will need to be editable to be able to personalize them for each new employee.
Nice to have
• The MapOut, ShipWell, KeepSteady would be okay to have if they can be sensibly and professionally added to the look without detracting from the main imagery.
• Maybe they could go on the back of the card? will leave this to your creative discretion as to whether/where they fit.
Should not have
• Should not have decorative or script fonts

```html
<!DOCTYPE html>
<html lang="en">
<head>
<meta charset="utf-8">
<title>KorvalIT Business Card</title>
<link rel="stylesheet" href="https://fonts.googleapis.com/css2?family=Raleway:wght@600;700&family=Roboto:wght@400&display=swap">
<style>
  :root {
    --backdrop: #e6e6e6;
    --card-white: #ffffff;
    --brand-red: #d71920;
    --charcoal: #3a3a3c;
    --text-light: #ffffff;
    --rule: #8a8a8a;
    --ship-blue: #1b87c9;
    --keep-magenta: #b0228c;
    --map-green: #5ea52e;
  }
  * { margin: 0; padding: 0; box-sizing: border-box; }
  html, body { width: 1200px; height: 802px; overflow: hidden; }
  body {
    background: var(--backdrop);
    position: relative;
    font-family: "Roboto", Arial, sans-serif;
  }
  .card {
    position: absolute;
    top: 274px;
    width: 442px;
    height: 264px;
    overflow: hidden;
  }
  .card-front { left: 135px; background: var(--brand-red); }
  .card-back { left: 624px; background: var(--card-white); }

  .front-panel {
    position: absolute;
    left: 0; top: 0;
    width: 129px; height: 100%;
    background: var(--charcoal);
  }
  .details {
    position: absolute;
    right: 27px;
    top: 0;
    text-align: right;
    color: var(--text-light);
  }
  .person-name {
    position: absolute; right: 0; top: 34px;
    white-space: nowrap;
    font-family: "Raleway", Arial, sans-serif;
    font-weight: 700;
    font-size: 16px;
    letter-spacing: -0.2px;
  }
  .person-role {
    position: absolute; right: 0; top: 52px;
    white-space: nowrap;
    font-size: 12.5px;
  }
  .address {
    position: absolute; right: 0; top: 95px;
    white-space: nowrap;
    font-size: 12.5px;
    line-height: 16px;
  }
  .contact-list {
    position: absolute; right: 0; top: 164px;
    list-style: none;
    font-size: 12.5px;
    line-height: 15.7px;
  }
  .contact-list li {
    display: flex;
    justify-content: flex-end;
    align-items: center;
    white-space: nowrap;
  }
  .contact-list svg {
    width: 9px; height: 9px;
    margin-left: 3px;
    fill: var(--text-light);
  }

  .main-brand {
    position: absolute;
    left: 0; right: 0; top: 92px;
    display: flex;
    justify-content: center;
    align-items: center;
    gap: 12px;
  }
  .brand-square {
    width: 30px; height: 30px;
    background: var(--brand-red);
  }
  .brand-name {
    font-family: "Raleway", Arial, sans-serif;
    font-weight: 600;
    font-size: 39px;
    color: var(--charcoal);
    line-height: 1;
  }
  .divider {
    position: absolute;
    left: 59px; width: 325px; top: 190px;
    height: 1px;
    background: var(--rule);
  }
  .service-brands {
    position: absolute;
    left: 0; right: 0; top: 208px;
    display: flex;
    justify-content: center;
    gap: 12px;
    list-style: none;
  }
  .service {
    display: flex;
    align-items: center;
    gap: 5px;
    font-family: "Raleway", Arial, sans-serif;
    font-weight: 600;
    font-size: 18px;
    line-height: 1;
  }
  .service::before {
    content: "";
    width: 13px; height: 13px;
    background: currentColor;
  }
  .service-ship { color: var(--ship-blue); }
  .service-keep { color: var(--keep-magenta); }
  .service-map { color: var(--map-green); }
</style>
</head>
<body>
  <section class="card card-front" aria-label="Card front">
    <div class="front-panel"></div>
    <div class="details">
      <h1 class="person-name">DANA WHITLOCK</h1>
      <p class="person-role">Business Development Manager</p>
      <p class="address">Level 1, 47 Fernby Street<br>Carlow Qld 4072</p>
      <ul class="contact-list">
        <li>+61 (0)412 555 018
          <svg viewBox="0 0 10 10" aria-hidden="true"><path d="M0 4 Q5 0 10 4 L8 5 L7 4 L3 4 L2 5 Z M2 5 L8 5 L9 9 L1 9 Z"/></svg></li>
        <li>+61 (0)7 3555 0142
          <svg viewBox="0 0 10 10" aria-hidden="true"><path d="M2.5 0 H7.5 V10 H2.5 Z M3.5 1 V8 H6.5 V1 Z"/></svg></li>
        <li>+61 (0)7 3555 0143
          <svg viewBox="0 0 10 10" aria-hidden="true"><path d="M2 0 H8 V3 H2 Z M0 3.5 H10 V8 H8 V10 H2 V8 H0 Z"/></svg></li>
        <li>dwhitlock@korvalit.com.au
          <svg viewBox="0 0 10 10" aria-hidden="true"><path d="M0 2 H10 V8 H0 Z" /><path d="M0.5 2.5 L5 6 L9.5 2.5" stroke="#d71920" stroke-width="1" fill="none"/></svg></li>
        <li>www.korvalit.com.au
          <svg viewBox="0 0 10 10" aria-hidden="true"><circle cx="5" cy="5" r="5"/><path d="M0.5 5 H9.5 M5 0.5 Q2 5 5 9.5 M5 0.5 Q8 5 5 9.5" stroke="#d71920" stroke-width="0.8" fill="none"/></svg></li>
      </ul>
    </div>
  </section>

  <section class="card card-back" aria-label="Card back">
    <div class="main-brand">
      <span class="brand-square" aria-hidden="true"></span>
      <span class="brand-name">KorvalIT</span>
    </div>
    <div class="divider"></div>
    <ul class="service-brands">
      <li class="service service-ship">ShipWell</li>
      <li class="service service-keep">KeepSteady</li>
      <li class="service service-map">MapOut</li>
    </ul>
  </section>
</body>
</html>
```